Etiketten-Design für einen importierten Honig
Zielgruppe
Wir importieren originalen Manuka Honig aus Neuseeland. Der Manuka Honig ist bekannt für seine besonderen Eigenschaften (antibakteriell, etc.). Ein Glas unseres Honigs (500g) kostet zwischen 30 und 150 EUR.
Unsere Zielgruppe sind gesundheitsbewusste Kunden, die wenig preissensibel sind. Überwiegend wird der Manuka Honig im Fachhandel (z.B. Reformhaus, Drogerie, Biomarkt, etc.) verkauft. Der Großteil unserer Kunden ist 30+ Jahre.
Aufgabenstellung
Bei dem Etikett handelt es sich um das erste Produktetikett. Damit ist in der Farbgestaltung noch alles offen. Das Logo und der Name ist jedoch fix.
Das Etikett ist wird auf einem bpa-freien schwarzen Plastikbehälter angebracht. Dieser ist bei Manuka Honigen Standard aufgrund des langen Transports von Neuseeland nach Deutschland (gerne googeln). Der Deckel dieses Behälters ist schwarz.
Nachdem es sich um ein hochpreisiges Produkt handelt, soll das Etikett diese hohe Wertigkeit widerspiegeln. Damit ist eine Veredelung des Etiketts notwendig. Viele Konkurrenten arbeiten mit Gold, alternative Farben sind jedoch auch möglich.
Das Etikett überdeckt drei der vier Seiten des Plastikbehälters (vorne + links + rechts). Die Maße sind 160 mm x 60 mm. Zusätzlich zu den Etikettenmaßen bitte 2 mm Beschnittzugabe je Seite hinzufügen.
Hintergrundinformationen zu unserer Marke:
- Der Markenname lautet Kalvio. Der Markenname leitet sich von der ersten Imkerin Neuseelands ab - Edith Carrow. Sie hatte im Jahr 1839 die ersten Bienenstöcke nach Neuseeland gebracht und den ersten Manuka Honig geerntet.
- Unser Logo ist eine Verbindung einer Frau und den neuseeländischen Farn. Dieses Logo stellt also direkt eine Verbindung zu Neuseeland dar.
- Unsere Marke Kalvio ist eine qualitativ hochwertige, luxuriöse und hochpreisige Marke. Genau wie in dem Logo selbst, sollen diese Verbindungen zu Neuseeland, der Natur (Honig ist ein Naturprodukt) und Edith Carrow auch auf dem Etikett zu finden sein.
Wonach suchen wir:
- Wir sind auf der Suche nach einem einzigartigen Design, der unseren Honig besonders hervorhebt. Das Etikett soll auffällig sein und uns von anderen unterscheiden. (Eye-catching)
- Eine Veredelung des Etiketts ist Pflicht, da dies für uns die Wertigkeit des Etiketts und des Produktes stark erhöht. In welcher Art die Veredelung durchgeführt wird, ist Ihnen überlassen.
Das dürfen Sie frei wählen:
- Bisher haben..

```html
<!DOCTYPE html>
<html lang="de">
<head>
<meta charset="utf-8">
<title>Kalvio Manuka Honig – Etikett</title>
<link rel="stylesheet" href="https://fonts.googleapis.com/css2?family=Lato:wght@400;700;900&display=swap">
<style>
  :root {
    --page: #ffffff;
    --label: #2e2e2e;
    --front: #323232;
    --front-light: #3d3d3d;
    --gold: #eaa623;
    --gold-light: #f4c451;
    --text: #f2f2f2;
    --muted: #e4e4e4;
    --paper: #ffffff;
  }
  * { box-sizing: border-box; margin: 0; padding: 0; }
  html, body { width: 1200px; height: 751px; overflow: hidden; background: var(--page); }
  body { font-family: "Lato", sans-serif; color: var(--text); position: relative; }

  .label {
    position: absolute; left: 120px; top: 237px;
    width: 962px; height: 365px;
    background: var(--label);
    overflow: hidden;
  }
  .panel { position: absolute; top: 0; height: 100%; }
  .panel--side-left { left: 0; width: 315px; }
  .panel--front {
    left: 315px; width: 324px;
    background: linear-gradient(90deg, var(--front) 0%, var(--front-light) 18%, var(--front) 40%, var(--front) 100%);
  }
  .panel--side-right { left: 639px; width: 323px; }

  /* Nährwerte */
  .nutrition-title {
    position: absolute; left: 49px; width: 218px; top: 16px;
    font-size: 12px; font-weight: 700; text-align: center; letter-spacing: .2px;
    padding-bottom: 4px; border-bottom: 2px solid var(--gold);
  }
  .nutrition-table {
    position: absolute; left: 49px; width: 218px; top: 38px;
    border-collapse: collapse; font-size: 12px;
  }
  .nutrition-table td { height: 14.6px; line-height: 14.6px; padding: 0; white-space: nowrap; }
  .nutrition-table td:last-child { text-align: right; }
  .nutrition-table .sub td:first-child { padding-left: 9px; }
  .storage {
    position: absolute; left: 0; width: 315px; top: 148px;
    font-size: 10.5px; line-height: 13px; text-align: center; color: var(--muted);
  }
  .infant-warning {
    position: absolute; left: 0; width: 315px; top: 188px;
    font-size: 10.5px; line-height: 13px; text-align: center; text-transform: uppercase; letter-spacing: .2px;
  }
  .lot-field {
    position: absolute; left: 45px; top: 224px; width: 224px; height: 141px;
    background: var(--paper);
  }

  /* Vorderseite */
  .brand {
    position: absolute; left: 0; width: 210px; top: 50px;
    display: flex; flex-direction: column; align-items: center; gap: 10px;
  }
  .brand__dot { width: 70px; height: 70px; border-radius: 50%; border: 2px solid var(--gold); }
  .brand__name { font-size: 21px; font-weight: 400; color: var(--gold); letter-spacing: 1.5px; text-transform: uppercase; }

  .heritage-illustration {
    position: absolute; left: 166px; top: 35px; width: 150px; height: 330px;
    background: linear-gradient(180deg, rgba(20,20,20,.25), rgba(15,15,15,.55));
    border-radius: 60px 60px 0 0;
  }
  .product-name {
    position: absolute; left: 27px; top: 196px;
    font-weight: 900; color: #fff; line-height: 1; text-transform: uppercase;
  }
  .product-name__line1 { display: block; font-size: 37px; letter-spacing: .5px; }
  .product-name__line2 { display: block; font-size: 47px; margin-top: 3px; }
  .product-grade { display: block; font-size: 31px; font-weight: 700; color: var(--gold); margin-top: 4px; letter-spacing: .5px; }
  .product-origin { display: block; font-size: 14.5px; font-weight: 700; letter-spacing: 3.2px; margin-top: 4px; }

  /* Rechte Seite */
  .story-title {
    position: absolute; left: 0; width: 323px; top: 16px;
    text-align: center; font-size: 16px; font-weight: 900; color: var(--gold);
    letter-spacing: 1.8px; line-height: 18.5px; text-transform: uppercase;
  }
  .story-text {
    position: absolute; left: 10px; width: 303px; top: 60px;
    text-align: center; font-size: 13px; font-weight: 700; line-height: 15.5px; letter-spacing: .3px;
  }
  .story-text p + p { margin-top: 8px; }
  .divider {
    position: absolute; left: 103px; width: 148px; top: 239px; height: 2px;
    background: linear-gradient(90deg, #111, #1a1a1a 70%, #555 80%, #111);
  }
  .contents, .importer {
    position: absolute; left: 0; width: 323px; text-align: center;
    font-size: 10.5px; line-height: 13px; color: var(--muted); letter-spacing: .2px;
  }
  .contents { top: 257px; }
  .importer { top: 278px; }
  .net-weight {
    position: absolute; left: 0; width: 323px; top: 328px;
    text-align: center; font-size: 18px; font-weight: 700;
  }
</style>
</head>
<body>
  <main class="label">
    <section class="panel panel--side-left">
      <h2 class="nutrition-title">NÄHRWERTANGABEN PRO 100 g</h2>
      <table class="nutrition-table">
        <tr><td>Energie</td><td>1400 kJ / 329 kcal</td></tr>
        <tr><td>Fett</td><td>0,8 g</td></tr>
        <tr class="sub"><td>davon gesättigte Fettsäuren</td><td>0,5 g</td></tr>
        <tr><td>Kohlenhydrate</td><td>80,4 g</td></tr>
        <tr class="sub"><td>davon Zucker</td><td>65,4 g</td></tr>
        <tr><td>Eiweiß</td><td>0,1 g</td></tr>
        <tr><td>Salz</td><td>0,02 g</td></tr>
      </table>
      <p class="storage">1 Portion = 10g,<br>Trocken, dunkel und nicht über 25 °C lagern.</p>
      <p class="infant-warning">Honig ist für Säuglinge unter<br>12 Monaten nicht geeignet</p>
      <div class="lot-field"></div>
    </section>

    <section class="panel panel--front">
      <div class="heritage-illustration" role="img" aria-label="Linienzeichnung der ersten Imkerin Neuseelands mit Manukablüten"></div>
      <div class="brand">
        <span class="brand__dot"></span>
        <span class="brand__name">Kalvio</span>
      </div>
      <h1 class="product-name">
        <span class="product-name__line1">Manuka</span>
        <span class="product-name__line2">Honig</span>
        <span class="product-grade">MGO 450+</span>
        <span class="product-origin">Aus Neuseeland</span>
      </h1>
    </section>

    <section class="panel panel--side-right">
      <h2 class="story-title">Manuka Honig –<br>Das Gold der Maori</h2>
      <div class="story-text">
        <p>Bereits die Ureinwohner Neuseelands, die Maori, wussten um die Kostbarkeit des Manuka Honigs und nutzten ihn für seine besonderen Eigenschaften.</p>
        <p>Der Anteil des in diesem Honig enthaltenen Wirkstoffs Methylglyoxal (MGO) wurde durch ein akkreditiertes Labor auf mindestens 450 mg/kg geprüft.</p>
      </div>
      <div class="divider"></div>
      <p class="contents">Inhalt: 100 % Manuka Honig aus Neuseeland</p>
      <p class="importer">Importiert und vertrieben durch:<br>Velmora GmbH, Lindenweg 12,<br>95111 Grünhain</p>
      <p class="net-weight">℮ 500g</p>
    </section>
  </main>
</body>
</html>
```